Dunmore Roofing

Want a professional looking business card

Industry/Entity Type

Business

Contact Information for Business Card

Paul Dunmore ( Owner) paul@dunmoreroofing-example.com, www.dunmoreroofing-example.com, Adress: 4172 Township road 43 Plantagenet,ON K9X4T2

```html
<!DOCTYPE html>
<html lang="en">
<head>
<meta charset="utf-8">
<title>Dunmore Roofing – Business Card</title>
<link rel="stylesheet" href="https://fonts.googleapis.com/css2?family=Roboto:wght@400;500&family=Roboto+Condensed:wght@400;500;700&display=swap">
<style>
  :root {
    --backdrop: #232323;
    --card: #f2f2f2;
    --brand-blue: #183f7e;
    --slate: #6f6f72;
    --white: #ffffff;
    --ink-soft: #4a4a4c;
  }
  * { margin: 0; padding: 0; box-sizing: border-box; }
  html, body {
    width: 1200px; height: 960px; overflow: hidden;
    background: var(--backdrop);
  }
  .stage { position: relative; width: 1200px; height: 960px; }

  .card {
    position: absolute;
    width: 600px; height: 343px;
    background: var(--card);
    overflow: hidden;
  }
  .card--front { left: 314px; top: 113px; }
  .card--back  { left: 311px; top: 472px; }

  .front__panel { position: absolute; inset: 0; }

  .accent-square {
    position: absolute; left: 16px;
    width: 45px; height: 45px;
    background: var(--slate);
  }
  .accent-square--upper { top: 205px; }
  .accent-square--lower { top: 265px; }

  .front__content {
    position: absolute; right: 46px; top: 0;
    text-align: right; color: var(--white);
  }
  .wordmark {
    font-family: "Roboto Condensed", sans-serif;
    font-weight: 700;
    text-transform: uppercase;
    letter-spacing: 1px;
    white-space: nowrap;
  }
  .front__wordmark {
    margin-top: 58px;
    font-size: 32px;
    line-height: 32px;
    color: var(--white);
  }
  .holder-name {
    margin-top: 53px;
    font-family: "Roboto Condensed", sans-serif;
    font-weight: 500;
    font-size: 25px;
    line-height: 25px;
  }
  .holder-role {
    margin-top: 6px;
    font-family: "Roboto", sans-serif;
    font-size: 15px;
    line-height: 15px;
  }
  .address {
    margin-top: 8px;
    font-family: "Roboto", sans-serif;
    font-size: 15px;
    line-height: 19px;
    font-style: normal;
  }
  .contact-list {
    list-style: none;
    margin-top: 8px;
    font-family: "Roboto", sans-serif;
    font-size: 15px;
    line-height: 19px;
  }
  .contact-list li {
    display: flex; justify-content: flex-end; align-items: center; gap: 7px;
    white-space: nowrap;
  }
  .contact-list svg { width: 14px; height: 14px; fill: var(--white); flex: none; }

  .back__content {
    position: absolute; left: 0; right: 0; top: 0;
    text-align: center;
  }
  .back__wordmark {
    margin-top: 180px;
    font-size: 40px;
    line-height: 1;
    color: var(--brand-blue);
  }
  .back__site {
    margin-top: 66px;
    font-family: "Roboto", sans-serif;
    font-size: 15px;
    letter-spacing: 4.2px;
    color: var(--ink-soft);
    white-space: nowrap;
  }
</style>
</head>
<body>
<main class="stage">
  <section class="card card--front">
    <svg class="front__panel" viewBox="0 0 600 343" width="600" height="343" aria-hidden="true">
      <polygon points="0,0 600,0 600,343 306,343" fill="var(--brand-blue)"/>
    </svg>
    <div class="accent-square accent-square--upper"></div>
    <div class="accent-square accent-square--lower"></div>

    <div class="front__content">
      <p class="wordmark front__wordmark">Dunmore Roofing</p>
      <p class="holder-name">PAUL DUNMORE</p>
      <p class="holder-role">OWNER</p>
      <address class="address">4172 Township road 43<br>Ashcombe, NB K9X4T2</address>
      <ul class="contact-list">
        <li>613 555 0148
          <svg viewBox="0 0 24 24"><path d="M6.6 10.8a15.1 15.1 0 0 0 6.6 6.6l2.2-2.2a1 1 0 0 1 1-.25 11.4 11.4 0 0 0 3.6.57 1 1 0 0 1 1 1V20a1 1 0 0 1-1 1A17 17 0 0 1 3 4a1 1 0 0 1 1-1h3.5a1 1 0 0 1 1 1c0 1.25.2 2.45.57 3.57a1 1 0 0 1-.25 1z"/></svg>
        </li>
        <li>paul@dunmoreroofing-example.com
          <svg viewBox="0 0 24 24"><path d="M2 5h20v2l-10 6L2 7zM2 9l10 6 10-6v10H2z"/></svg>
        </li>
        <li>www.dunmoreroofing-example.com
          <svg viewBox="0 0 24 24"><circle cx="12" cy="12" r="10"/><path d="M7 7c2 0 3 1 3 3s-2 2-2 4 2 2 2 4M15 5c-1 2 1 3 2 4s2 3 0 5" stroke="var(--brand-blue)" stroke-width="1.8" fill="none"/></svg>
        </li>
      </ul>
    </div>
  </section>

  <section class="card card--back">
    <div class="back__content">
      <p class="wordmark back__wordmark">Dunmore Roofing</p>
      <p class="back__site">www.dunmoreroofing-example.com</p>
    </div>
  </section>
</main>
</body>
</html>
```